Q&J RESTORATION

I want a brochure similiar to the example i've attached.
My company name is Q&J Restoration. The website is: Q-J-Restoration.example.
The phone number is 919.555.0147.

I don't like the "yellow" being the main color of the example so I'm open to suggestions. I want something CLEAN & Simple, like our logo . This will be a bi fold brochure

```html
<!DOCTYPE html>
<html lang="en">
<head>
<meta charset="utf-8">
<title>Q&amp;J Restoration – Bi-fold Brochure</title>
<link rel="stylesheet" href="https://fonts.googleapis.com/css2?family=Montserrat:wght@400;500;600;700;800&display=swap">
<style>
:root{
  --page:#f4f4f4;
  --ink:#0b0b0b;
  --panel-top:#2a2a2a;
  --panel-mid:#141414;
  --panel-deep:#050505;
  --white:#ffffff;
  --soft:#d9d9d9;
  --muted:#9a9a9a;
  --rule:#6d6d6d;
}
*{margin:0;padding:0;box-sizing:border-box}
html,body{width:1200px;height:2515px;overflow:hidden;background:var(--page)}
body{position:relative;font-family:"Montserrat",Arial,sans-serif;color:var(--white)}
.spread{position:absolute;left:150px;width:900px;height:694px;overflow:hidden;box-shadow:0 6px 14px rgba(0,0,0,.35)}
.spread--cover{top:520px}
.spread--inside{top:1290px}
.backdrop{position:absolute;inset:0}
.spread--cover .backdrop{background:linear-gradient(180deg,var(--panel-mid) 0%,#3a3a3a 45%,var(--panel-mid) 70%,var(--panel-deep) 100%)}
.spread--inside .backdrop{background:linear-gradient(180deg,#232323 0%,#333 40%,#242424 75%,#1c1c1c 100%)}
.abs{position:absolute}
.bars span{display:block;width:86px;height:7px;background:var(--white);margin-bottom:23px}
.brand{border:2px solid var(--white);display:flex;align-items:center;gap:10px;font-weight:500;color:var(--white);letter-spacing:1px}
.brand i{display:block;width:12px;height:12px;background:var(--white)}
.brand--large{left:486px;top:58px;width:200px;height:83px;padding:0 16px;font-size:22px}
.brand--small{left:55px;top:439px;width:130px;height:43px;padding:0 10px;font-size:13px;gap:7px}
.brand--small i{width:8px;height:8px}
.brand--inside{left:705px;top:605px;width:150px;height:52px;padding:0 10px;font-size:15px;gap:8px}
.brand--inside i{width:9px;height:9px}
.hero-frame{left:201px;top:192px;width:657px;height:289px;background:var(--white);padding:12px}
.hero-photo{width:100%;height:100%;background:linear-gradient(90deg,#d9d1c0 0%,#a49a88 35%,#6f6a60 55%,#c9c1b2 80%,#b69d7a 100%)}
.tagline{left:555px;top:337px;width:305px;height:23px;background:var(--ink);font-size:13px;font-weight:600;letter-spacing:3px;display:flex;align-items:center;justify-content:center}
.claim{left:53px;top:572px}
.claim h3{font-size:21px;font-weight:800;line-height:20px}
.claim p{margin-top:4px;background:#bdbdbd;color:var(--ink);font-size:10.5px;font-weight:500;padding:1px 4px;letter-spacing:.5px;width:137px}
.contacts{left:228px;top:584px;font-size:9.5px;font-weight:500;list-style:none}
.contacts li{display:flex;align-items:center;gap:10px;height:19px}
.contacts svg{width:14px;height:14px}
.headline{left:484px;top:518px}
.headline .kicker{font-size:18px;font-weight:500;letter-spacing:5px;padding-bottom:6px;border-bottom:1px solid var(--rule);width:312px}
.headline .line1{font-size:31px;font-weight:800;margin-top:6px;line-height:32px;color:var(--soft)}
.headline .line2{font-size:45px;font-weight:800;line-height:44px;color:var(--soft)}
.headline .url{font-size:11px;letter-spacing:3.5px;margin-top:10px}
.side-frame{left:0;top:40px;width:345px;height:613px;background:var(--white);padding:12px 12px 12px 0}
.side-photo{width:100%;height:100%;background:linear-gradient(180deg,#5b5d62 0%,#a7b7c4 30%,#c9cfd2 55%,#6c8a4c 82%,#9aa58c 100%)}
.services{left:484px;top:43px;width:372px}
.services h2{font-size:26px;font-weight:800;color:var(--soft);margin-bottom:10px}
.service{display:flex;gap:14px;padding:10px 0 10px;border-bottom:1px dashed var(--rule)}
.service:last-child{border-bottom:none}
.service .icon{flex:0 0 46px;height:46px;border-radius:50%;border:2px solid var(--white);display:flex;align-items:center;justify-content:center}
.service .icon svg{width:24px;height:24px}
.service h4{font-size:14.5px;font-weight:600;margin-bottom:3px}
.service p{font-size:8.6px;line-height:10.8px;color:var(--soft)}
.thumbs{left:484px;top:479px;display:flex;gap:10px}
.thumb{width:118px;height:111px;background:var(--white);padding:4px}
.thumb div{width:100%;height:100%}
.thumb--duct div{background:linear-gradient(180deg,#8c8373,#5a4e3c 60%,#a08c64)}
.thumb--mold div{background:linear-gradient(135deg,#cfd2d4,#8b8f93 60%,#c2c5c7)}
.thumb--water div{background:linear-gradient(180deg,#c39a63,#6b4b2b 60%,#9b7b55)}
.closing{left:484px;top:620px}
.closing h3{font-size:22px;font-weight:800;color:var(--soft);line-height:22px}
.closing p{font-size:13.5px;font-weight:700}
</style>
</head>
<body>

<section class="spread spread--cover">
  <div class="backdrop" role="img" aria-label="Dark faded interior of a dining room behind the cover"></div>
  <div class="abs brand brand--large"><i></i>Q&amp;J Restoration</div>
  <div class="abs bars" style="left:78px;top:194px"><span></span><span></span><span></span></div>
  <div class="abs hero-frame"><div class="hero-photo" role="img" aria-label="Photo of a bright modern dining room with shelving divider"></div></div>
  <div class="abs tagline">BUILD.RENOVATE.RESTORE</div>
  <div class="abs brand brand--small"><i></i>Q&amp;J Restoration</div>
  <div class="abs claim"><h3>INSURANCE<br>CLAIM?</h3><p>WE'RE ON YOUR TEAM</p></div>
  <ul class="abs contacts">
    <li><svg viewBox="0 0 14 14"><circle cx="7" cy="7" r="7" fill="#fff"/><path d="M4.3 3.6l1.4-.3.7 1.8-.9.6a5 5 0 0 0 2.8 2.8l.6-.9 1.8.7-.3 1.4C8 10 4 6 4.3 3.6z" fill="#111"/></svg>919.555.0147</li>
    <li><svg viewBox="0 0 14 14"><circle cx="7" cy="7" r="7" fill="#fff"/><rect x="3.5" y="4.5" width="7" height="5" fill="none" stroke="#111" stroke-width="1"/><path d="M3.5 4.5L7 7.3l3.5-2.8" fill="none" stroke="#111" stroke-width="1"/></svg>QJrestoration15@mail.example</li>
    <li><svg viewBox="0 0 14 14"><circle cx="7" cy="7" r="7" fill="#fff"/><circle cx="7" cy="7" r="3.8" fill="none" stroke="#111" stroke-width="1"/><path d="M3.2 7h7.6M7 3.2c-2 2.2-2 5.4 0 7.6M7 3.2c2 2.2 2 5.4 0 7.6" fill="none" stroke="#111" stroke-width=".8"/></svg>www.Q-J-Restoration.example</li>
  </ul>
  <div class="abs headline">
    <div class="kicker">THREE GENERATIONS OF</div>
    <div class="line1">RESTORATION</div>
    <div class="line2">EXPERIENCE</div>
    <div class="url">www.Q-J-Restoration.example</div>
  </div>
</section>

<section class="spread spread--inside">
  <div class="backdrop" role="img" aria-label="Dark faded interior of a living room behind the inside pages"></div>
  <div class="abs side-frame"><div class="side-photo" role="img" aria-label="Photo of a couple walking in front of a modern home"></div></div>
  <div class="abs bars" style="left:364px;top:40px"><span></span><span></span><span></span></div>
  <div class="abs services">
    <h2>OUR SERVICES</h2>
    <div class="service">
      <div class="icon"><svg viewBox="0 0 24 24" fill="none" stroke="#fff" stroke-width="1.5"><rect x="3" y="6" width="18" height="12"/><path d="M6 9h12M6 12h12M6 15h12"/></svg></div>
      <div><h4>Duct Cleaning</h4><p>Keep the air quality in your home clean. Cleaning your air ducts can help minimize allergies, asthma, and other sicknesses related to poor air quality. Cleaning your air ducts is one of the primary ways to keep the air clean in your home to keep you and your family safe and healthy.</p></div>
    </div>
    <div class="service">
      <div class="icon"><svg viewBox="0 0 24 24" fill="none" stroke="#fff" stroke-width="1.5"><rect x="5" y="3" width="14" height="18" rx="1"/><circle cx="12" cy="13" r="4"/><path d="M5 7h14"/></svg></div>
      <div><h4>Dryer Vent Cleaning</h4><p>A clogged dryer vent can cost you loads of money through high electricity bills and dryer over heating. Also, the lint that forms inside the vent is harmful to your property and your family. We recommend cleaning your dryer vent every two to three years.</p></div>
    </div>
    <div class="service">
      <div class="icon"><svg viewBox="0 0 24 24" fill="none" stroke="#fff" stroke-width="1.5"><path d="M3 9h7v6H3zM14 9h7v6h-7zM10 12h4M12 3v6"/><path d="M12 17c-1 1.5-1.5 2.3-1.5 3a1.5 1.5 0 0 0 3 0c0-.7-.5-1.5-1.5-3z"/></svg></div>
      <div><h4>Water Damage Restoration</h4><p>Broken pipes, leaks or a recent flood? Should your home experience a water damage loss, big or small; call Q&amp;J Restoration immediately to limit the damage to your property and expense of restoration.</p></div>
    </div>
    <div class="service">
      <div class="icon"><svg viewBox="0 0 24 24" fill="none" stroke="#fff" stroke-width="1.5"><path d="M4 20V9l8-5 8 5v11z"/><circle cx="9" cy="13" r="1.5"/><circle cx="15" cy="15" r="1.5"/><circle cx="12" cy="18" r="1"/></svg></div>
      <div><h4>Mold Remediation</h4><p>Mold can develop in almost any home or office is a very small amount of time and moisture. Mold can spread within a house within 48-72 hours of developing. This can lead to potential health risks and irritants for everyone in the house.</p></div>
    </div>
  </div>
  <div class="abs thumbs">
    <div class="thumb thumb--duct"><div role="img" aria-label="Photo of the inside of a dusty air duct"></div></div>
    <div class="thumb thumb--mold"><div role="img" aria-label="Photo of a worker in protective suit removing mold"></div></div>
    <div class="thumb thumb--water"><div role="img" aria-label="Photo of a flooded floor being cleaned"></div></div>
  </div>
  <div class="abs closing"><h3>HERE FOR YOU</h3><p>EVERY STEP OF THE WAY</p></div>
  <div class="abs brand brand--inside"><i></i>Q&amp;J Restoration</div>
</section>

</body>
</html>
```